Request for Business Card Design

Hi. My name is Marlene, I am looking for a new business card design for my company, Quarrow Signal Instruments, LLC. I really like the design you did for Tarsel Venture and was hoping you could do something similar using our full logo and our mark. I am also open to any raised texture design using our mark. I have attached our full logo, which would need to be somewhere on the card, as well as the mark in both outline and full form, as well as our brand colors / guide. The card does not have to be white, as long as our logo and mark appear. I actually like darker colored business cards more, but am open to all options. If you are interested in working with me, please let me know. We would also take the business card design into letterhead design if you can do that.

```html
<!DOCTYPE html>
<html lang="en">
<head>
<meta charset="utf-8">
<title>Quarrow Signal Instruments – Business Card</title>
<link href="https://fonts.googleapis.com/css2?family=Barlow:wght@600&family=Open+Sans:wght@400;700&display=swap" rel="stylesheet">
<style>
  :root {
    --backdrop: #3b3b3b;
    --card: #141414;
    --accent: #1c9bd7;
    --ink: #ffffff;
    --ink-soft: #d9d9d9;
    --emboss-light: #a9a9a9;
    --emboss-dark: #1a1a1a;
  }
  * { margin: 0; padding: 0; box-sizing: border-box; }
  html, body { width: 1200px; height: 801px; overflow: hidden; }
  body {
    background: var(--backdrop);
    font-family: "Open Sans", sans-serif;
    color: var(--ink);
    position: relative;
  }
  .card {
    position: absolute;
    width: 540px;
    height: 309px;
    background: var(--card);
    border-bottom: 3px solid var(--accent);
    overflow: hidden;
  }
  .card--front { left: 40px; top: 246px; }
  .card--back  { left: 620px; top: 246px; }

  /* wordmark */
  .wordmark { position: absolute; display: flex; align-items: center; gap: 12px; }
  .wordmark__dot { width: 26px; height: 26px; border-radius: 50%; background: var(--accent); flex: none; }
  .wordmark__text { font-family: "Barlow", sans-serif; font-weight: 600; color: var(--ink); line-height: 1; }
  .wordmark__name { display: block; font-size: 40px; letter-spacing: 3px; }
  .wordmark__sub  { display: block; font-size: 11px; letter-spacing: 0.6px; margin-top: 2px; }
  .card--front .wordmark { left: 30px; top: 128px; }

  /* person block */
  .person { position: absolute; right: 30px; top: 28px; text-align: right; }
  .person__name { color: var(--accent); font-weight: 700; font-size: 19px; letter-spacing: 0.5px; }
  .person__role { font-size: 12px; color: var(--ink-soft); margin-top: 2px; }
  .divider { position: absolute; height: 1px; background: var(--accent); }
  .divider--top { right: 30px; top: 86px; width: 220px; }
  .divider--bottom { left: 30px; right: 30px; top: 222px; }
  .address { position: absolute; right: 30px; top: 98px; text-align: right; font-size: 12.5px; line-height: 1.6; color: var(--ink-soft); }

  .contacts { position: absolute; left: 30px; top: 232px; list-style: none; font-size: 12px; line-height: 20px; color: var(--ink-soft); }
  .contacts li { display: flex; align-items: center; gap: 9px; }
  .contacts svg { width: 11px; height: 11px; fill: var(--accent); flex: none; }

  /* back */
  .emboss {
    position: absolute; right: -40px; top: -60px;
    width: 340px; height: 340px; border-radius: 50%;
    background: radial-gradient(circle at 75% 60%, var(--emboss-light), #4a4a4a 45%, var(--emboss-dark) 80%);
    opacity: 0.85;
  }
  .card--back .wordmark { left: 30px; bottom: 30px; }
</style>
</head>
<body>

<section class="card card--front" aria-label="Business card front">
  <div class="wordmark">
    <span class="wordmark__dot"></span>
    <span class="wordmark__text">
      <span class="wordmark__name">QUARROW</span>
      <span class="wordmark__sub">SIGNAL INSTRUMENTS</span>
    </span>
  </div>

  <div class="person">
    <p class="person__name">TOBIN ASHGROVE</p>
    <p class="person__role">President</p>
  </div>
  <div class="divider divider--top"></div>
  <p class="address">1180 Ferrow Cove Drive<br>Lindale Bay CA 90412</p>

  <div class="divider divider--bottom"></div>
  <ul class="contacts">
    <li><svg viewBox="0 0 12 12"><path d="M2.5 0.8 4.4 3 3.4 4.3a7 7 0 0 0 4.3 4.3L9 7.6l2.2 1.9-1.3 1.7C5.4 11.3.8 6.6.8 2.1z"/></svg>555-310-4720</li>
    <li><svg viewBox="0 0 12 12"><path d="M0.5 2.5h11v7h-11zM1.5 3.4 6 6.7l4.5-3.3v-.1h-9z"/></svg>t.ashgrove@quarrow.com</li>
    <li><svg viewBox="0 0 12 12"><path d="M6 .5a5.5 5.5 0 1 0 0 11 5.5 5.5 0 0 0 0-11zm0 1.3c.8.9 1.3 2.3 1.4 3.6H4.6C4.7 4.1 5.2 2.7 6 1.8zM4.6 6.6h2.8C7.3 7.9 6.8 9.3 6 10.2 5.2 9.3 4.7 7.9 4.6 6.6z"/></svg>www.quarrow.com</li>
  </ul>
</section>

<section class="card card--back" aria-label="Business card back">
  <div class="emboss" role="img" aria-label="Raised brand mark decoration"></div>
  <div class="wordmark">
    <span class="wordmark__text">
      <span class="wordmark__name">QUARROW</span>
      <span class="wordmark__sub">SIGNAL INSTRUMENTS</span>
    </span>
  </div>
</section>

</body>
</html>
```